kelvaro stationary business card and letterhead

THIS PROJECT IS TO DESIGN A BUSINESS CARD DOUBLE SIDES .

Reason: I AM WAITING FOR TESINU SUBMISION

Industry/Entity Type

Business

Font styles to use
Other font styles liked:
• Chose your font

```html
<!DOCTYPE html>
<html lang="en">
<head>
<meta charset="utf-8">
<title>Kelvaro Letterhead</title>
<link rel="stylesheet" href="https://fonts.googleapis.com/css2?family=Open+Sans:wght@400;600&display=swap">
<style>
  :root {
    --backdrop: #ebebeb;
    --paper: #f8f8f8;
    --accent-yellow: #f1c232;
    --band-dark: #454446;
    --ink: #6a6a6a;
    --ink-strong: #4a4a4a;
    --signature-tone: #d9d9d9;
  }
  * { margin: 0; padding: 0; box-sizing: border-box; }
  html, body {
    width: 1200px; height: 1000px; overflow: hidden;
    background: var(--backdrop);
    font-family: "Open Sans", Arial, sans-serif;
  }
  .letterhead {
    position: absolute; left: 280px; top: 46px;
    width: 640px; height: 908px;
    background: var(--paper);
    box-shadow: 0 2px 10px rgba(0,0,0,0.08);
    color: var(--ink);
  }
  .brand {
    position: absolute; left: 62px; top: 66px;
    display: flex; align-items: center; gap: 10px;
  }
  .brand-dot {
    width: 30px; height: 30px; border-radius: 50%;
    background: var(--accent-yellow);
  }
  .brand-text { display: flex; flex-direction: column; line-height: 1; }
  .brand-name {
    font-size: 28px; font-weight: 600; color: var(--ink-strong);
    letter-spacing: 0.5px;
  }
  .brand-tagline {
    margin-top: 4px; font-size: 8.5px; letter-spacing: 1.6px;
    text-transform: uppercase; color: var(--accent-yellow);
  }
  .contact {
    position: absolute; left: 462px; top: 124px; width: 140px;
    list-style: none; font-size: 8.5px; line-height: 12px; color: var(--ink-strong);
  }
  .contact li { display: flex; align-items: flex-start; gap: 5px; }
  .contact svg { flex: none; margin-top: 2px; }
  .letter-body {
    position: absolute; left: 62px; top: 212px; width: 480px;
    font-size: 9.5px; line-height: 14px;
  }
  .salutation { margin-bottom: 10px; }
  .letter-body p.para { margin-bottom: 14px; text-align: justify; }
  .closing { margin-top: 8px; }
  .signature {
    position: absolute; left: 370px; top: 706px;
    width: 130px; height: 44px; border-radius: 4px;
    background: var(--signature-tone);
  }
  .footer-band {
    position: absolute; left: 0; right: 0; top: 770px; height: 14px;
    display: flex;
  }
  .footer-band .band-yellow { width: 170px; background: var(--accent-yellow); }
  .footer-band .band-dark { flex: 1; background: var(--band-dark); }
  .footer-mark {
    position: absolute; right: 30px; bottom: 40px;
    width: 22px; height: 22px; border-radius: 50%;
    background: var(--accent-yellow);
  }
</style>
</head>
<body>
  <main class="letterhead">
    <header class="brand">
      <span class="brand-dot"></span>
      <div class="brand-text">
        <span class="brand-name">Kelvaro</span>
        <span class="brand-tagline">International Consulting</span>
      </div>
    </header>

    <ul class="contact">
      <li>
        <svg width="7" height="9" viewBox="0 0 7 9"><path d="M3.5 0a3.2 3.2 0 0 0-3.2 3.2C.3 5.6 3.5 9 3.5 9s3.2-3.4 3.2-5.8A3.2 3.2 0 0 0 3.5 0z" fill="var(--accent-yellow)"/></svg>
        <span>48 Orchard Lane, Brookfield,<br>20415, Norland</span>
      </li>
      <li>
        <svg width="7" height="8" viewBox="0 0 7 8"><rect x="1.5" y="0" width="4" height="8" rx="1" fill="var(--accent-yellow)"/></svg>
        <span>555-0142-88</span>
      </li>
      <li>
        <svg width="7" height="8" viewBox="0 0 7 8"><rect x="0" y="1" width="7" height="6" rx="1" fill="var(--accent-yellow)"/></svg>
        <span>555-0142-89</span>
      </li>
      <li>
        <svg width="7" height="8" viewBox="0 0 7 8"><rect x="0" y="1.5" width="7" height="5" fill="var(--accent-yellow)"/></svg>
        <span>hello@kelvaro.com</span>
      </li>
      <li>
        <svg width="7" height="8" viewBox="0 0 7 8"><circle cx="3.5" cy="4" r="3.2" fill="var(--accent-yellow)"/></svg>
        <span>www.kelvaro.com</span>
      </li>
    </ul>

    <section class="letter-body">
      <p class="salutation">Dear Client</p>
      <p class="para">Lorem ipsum dolor sit amet, consectetur adipiscing elit. Nulla sodales nisi vitae Lorem ipsum dolor sit amet, consectetur adipiscing elit. Suspendisse feugiat eros nisl, a facilisis risus eleifend sed. Aliquam mauris enim, fermentum eu lacinia sit amet, laoreet eu leo. Nullam eleifend nulla in libero tristique, ac vulputate odio tincidunt. Etiam non condimentum tortor. Integer suscipit neque nec odio porttitor cursus. Phasellus a sapien blandit, suscipit justo id, condimentum ante. Morbi tristique justo risus, id mattis dui molestie ut. Nullam volutpat ut quam commodo faucibus. Pellentesque urna est, interdum in elit quis, pharetra elementum orci. Nam pharetra velit molestie justo placerat scelerisque.</p>
      <p class="para">Nullam aliquam ligula ac sem aliquet varius. Nullam sed laoreet sapien. Fusce ultricies lobortis odio, sed imperdiet magna lacinia egestas. Morbi vitae varius nibh. Phasellus purus felis, congue id tempor quis, porttitor ut sem. Integer turpis nunc, posuere at quam interdum, interdum pharetra lectus. Fusce commodo sapien vel consequat tincidunt. Proin sed nisl dignissim, accumsan dui ut, luctus turpis. Praesent vulputate elementum nibh. Ut volutpat felis ut mi tincidunt, vitae accumsan quam porta. Sed malesuada bibendum lectus tempor ullamcorper. Nullam interdum diam velit, id porta elit congue quis.</p>
      <p class="para">Pellentesque habitant morbi tristique senectus et netus et malesuada fames ac turpis egestas. Donec quis fermentum massa. Vivamus auctor tincidunt tellus, vel iaculis elit sagittis sit amet. Morbi aliquam pharetra lobortis. Mauris non iaculis ipsum. Morbi tortor ipsum, suscipit a laoreet sed, tempus non risus. Maecenas rhoncus vehicula est, sagittis vulputate magna ullamcorper non. Sed dignissim sapien sed rhoncus imperdiet.</p>
      <p class="closing">Best regards,</p>
    </section>

    <div class="signature" role="img" aria-label="Handwritten signature of the sender"></div>

    <div class="footer-band">
      <span class="band-yellow"></span>
      <span class="band-dark"></span>
    </div>
    <span class="footer-mark"></span>
  </main>
</body>
</html>
```